Business Card Design Project - del varosi group

dear Sirs

we need business card design for our group ( DEL Varosi Group ) , i have got the Logo design of our group from pixel harbor in previous , so all need details relating to our group i think available with you, as well as the the chosen logo design

we hope to provide us with business card logo that to be appropaite and satisfactory to us .

thanks

note : logo design of our group is attached .
Updates

Reason: please extend the deadline of my project for additional 15 days because i didn't received appropriate design for our gruop yet . kindly beaware that i have received 77 design till now , supossed to send me 200-250 design at least . thanks

Target Market(s)

contents

name : Kerem EL Nadiri

position : Operation Manager

Industry/Entity Type

Business

Requirements
Must have

• person name

group logo
Nice to have
• logo color matching with back background

```html
<!DOCTYPE html>
<html lang="en">
<head>
<meta charset="utf-8">
<title>DEL Varosi Group — Business Card</title>
<link href="https://fonts.googleapis.com/css2?family=Didact+Gothic&display=swap" rel="stylesheet">
<style>
  :root {
    --brand-blue: #0d4f93;
    --brand-blue-soft: #6c9fd6;
    --ink: #3a3a3a;
    --ink-soft: #555a60;
    --paper: #fbfbfb;
    --backdrop: #e9ecef;
  }
  * { box-sizing: border-box; margin: 0; padding: 0; }
  html, body {
    width: 1067px;
    height: 1200px;
    overflow: hidden;
    background: var(--backdrop);
    font-family: "Didact Gothic", "Century Gothic", sans-serif;
  }
  .sheet {
    position: relative;
    width: 1067px;
    height: 1200px;
  }
  .card {
    position: absolute;
    left: 153px;
    width: 760px;
    height: 434px;
    box-shadow: 0 6px 18px rgba(0,0,0,0.18);
    overflow: hidden;
  }
  .card--front { top: 120px; background: var(--paper); }
  .card--back  { top: 646px; background: var(--brand-blue); }

  .holder-name {
    position: absolute;
    left: 50px;
    top: 62px;
    font-size: 34px;
    color: var(--ink);
    letter-spacing: 0.5px;
  }
  .name-rule {
    position: absolute;
    left: 0;
    right: 0;
    top: 108px;
    height: 5px;
    background: var(--brand-blue);
  }
  .contact-list {
    position: absolute;
    left: 45px;
    top: 174px;
    list-style: none;
    font-size: 16px;
    line-height: 26px;
    color: var(--ink-soft);
  }
  .brand-lockup {
    position: absolute;
    left: 476px;
    top: 186px;
    display: flex;
    align-items: center;
    gap: 10px;
    color: var(--brand-blue);
    font-size: 30px;
    letter-spacing: 1px;
    white-space: nowrap;
  }
  .brand-lockup .mark {
    width: 16px;
    height: 16px;
    background: var(--brand-blue);
    flex: none;
  }
  .footer-band {
    position: absolute;
    left: 0;
    right: 0;
    top: 309px;
    height: 60px;
    background: var(--brand-blue);
  }

  .card--back .brand-lockup {
    left: 0;
    right: 0;
    top: 0;
    bottom: 0;
    justify-content: center;
    gap: 22px;
    color: var(--brand-blue-soft);
    font-size: 58px;
    letter-spacing: 2px;
  }
  .card--back .brand-lockup .mark {
    width: 30px;
    height: 30px;
    background: var(--brand-blue-soft);
  }
</style>
</head>
<body>
  <main class="sheet">
    <section class="card card--front" aria-label="Business card front">
      <h1 class="holder-name">Kerem EL Nadiri</h1>
      <div class="name-rule"></div>
      <ul class="contact-list">
        <li>Phone: 0123 456 789</li>
        <li>Fax: 0123 456 789</li>
        <li>info@yourdomain.com</li>
        <li>www.yourdomain.com</li>
        <li>PO. Box: City name, etc.</li>
      </ul>
      <div class="brand-lockup">
        <span class="mark"></span>
        <span class="brand-name">DEL Varosi Group</span>
      </div>
      <div class="footer-band"></div>
    </section>

    <section class="card card--back" aria-label="Business card back">
      <div class="brand-lockup">
        <span class="mark"></span>
        <span class="brand-name">DEL Varosi Group</span>
      </div>
    </section>
  </main>
</body>
</html>
```